Resposive web site in 4 languages + image gallery + logo design

We need a web page, which will work on all devices.
I have uploaded web page concept.
Company name: Praxelun
Industry/Entity Type
It Company
Logo Text
quality matters
Coding
Coded - Design and coding required
Number of Pages Required
1 page

```html
<!DOCTYPE html>
<html lang="en">
<head>
<meta charset="utf-8">
<title>Praxelun</title>
<link href="https://fonts.googleapis.com/css2?family=Raleway:wght@500;600;700;800&family=Open+Sans:wght@400;600&display=swap" rel="stylesheet">
<style>
:root{
  --orange:#e8901a;
  --orange-dark:#d98212;
  --green:#1d8a63;
  --green-btn:#1f8c66;
  --brown:#3b2b1f;
  --text:#7a7a7a;
  --heading:#2d2d2d;
  --white:#fff;
}
*{box-sizing:border-box;margin:0;padding:0}
html,body{width:1200px;height:3020px;overflow:hidden}
body{font-family:"Open Sans",Arial,sans-serif;color:var(--text);background:var(--white);position:relative}
.section{position:absolute;left:0;width:1200px}
.abs{position:absolute}

/* header */
.site-header{top:0;height:100px;background:var(--white)}
.brand{left:90px;top:32px;display:flex;align-items:center;gap:9px;font-family:"Raleway",sans-serif;font-weight:800;font-size:20px;color:var(--orange);letter-spacing:.5px;white-space:nowrap}
.brand-dot{width:16px;height:16px;border-radius:50%;background:var(--orange)}
.main-nav{left:366px;top:42px;display:flex;gap:60px;font-family:"Raleway",sans-serif;font-weight:700;font-size:13px;color:#333;letter-spacing:.5px}
.lang{left:850px;top:40px;font-size:13px;color:#555}
.lang b{color:var(--green);font-weight:600;margin-left:14px}
.lang b::after{content:"";display:inline-block;margin-left:8px;border:4px solid transparent;border-top-color:var(--orange);vertical-align:middle}
.social-ring{left:1045px;top:24px;width:50px;height:50px;border:2px solid var(--orange);border-radius:50%}

/* hero */
.hero{top:100px;height:556px;background:linear-gradient(120deg,#5a3b26 0%,#b8805a 35%,#d8a27a 55%,#7a5034 80%,#3c2718 100%)}
.hero-title{top:236px;left:0;width:1200px;text-align:center;font-family:"Raleway",sans-serif;font-weight:800;font-size:40px;color:var(--white);letter-spacing:1px}
.btn-quote{top:306px;left:515px;width:171px;height:45px;background:var(--green-btn);color:var(--white);font-family:"Raleway",sans-serif;font-weight:700;font-size:13px;display:flex;align-items:center;justify-content:center;letter-spacing:.5px}
.hero-dots{top:518px;left:528px;display:flex;gap:18px}
.hero-dots span{width:12px;height:12px;border:2px solid var(--white);border-radius:50%}
.hero-dots .on{background:var(--orange);border-color:var(--orange)}

/* service sections */
.photo{left:80px;width:457px;height:358px}
.svc-title{left:590px;font-family:"Raleway",sans-serif;font-weight:600;font-size:32px;color:var(--orange);letter-spacing:1px}
.svc-text{left:590px;width:530px;font-size:13px;line-height:23.7px;text-align:justify}
.svc-list{left:596px;display:grid;grid-template-columns:185px 226px 150px;row-gap:25px;font-size:15px;color:#444;list-style:none}
.svc-list li{min-height:20px}
.svc-list li::before{content:"";display:inline-block;width:7px;height:7px;border-right:2px solid var(--orange);border-top:2px solid var(--orange);transform:rotate(45deg);margin-right:14px;vertical-align:2px}
.svc-list li:empty::before{display:none}

.woodworks{top:656px;height:434px}
.stoneworks{top:1090px;height:460px;background:var(--orange)}
.stoneworks .svc-title,.stoneworks .svc-text,.stoneworks .svc-list{color:var(--white)}
.stoneworks .svc-list li::before{border-color:var(--white)}
.restoration{top:1550px;height:443px}
.about{top:1993px;height:459px;background:var(--green);color:var(--white)}
.about .svc-title{color:var(--white)}
.about .svc-text{color:var(--white)}
.signoff{left:594px;font-family:"Raleway",sans-serif;font-weight:700;font-size:15px;line-height:48px}

/* contact */
.contact{top:2452px;height:455px;background:linear-gradient(135deg,#4a3424,#2e2118 60%,#47321f)}
.contact h2,.form-title{font-family:"Raleway",sans-serif;font-weight:700;font-size:28px;color:var(--white);letter-spacing:.5px}
.contact-item{left:82px;display:flex;gap:14px;align-items:center}
.contact-icon{width:44px;height:44px;border:2px solid var(--orange);border-radius:50%;display:flex;align-items:center;justify-content:center}
.contact-label{font-size:11px;font-weight:600;color:var(--orange);text-transform:uppercase}
.contact-value{font-size:17px;color:var(--white);line-height:22px}
.form-sub{font-family:"Raleway",sans-serif;font-size:15px;color:#d9cfc6}
.field{background:var(--white);border-radius:20px;font-size:11px;color:#999;padding:12px 20px}
.btn-send{left:495px;top:358px;width:624px;height:36px;border-radius:18px;background:var(--orange);color:var(--white);font-weight:600;font-size:13px;letter-spacing:1px;display:flex;align-items:center;justify-content:center}

/* footer */
.site-footer{top:2907px;height:113px;background:var(--orange);color:var(--white)}
.footer-brand{left:92px;top:42px;font-family:"Raleway",sans-serif;font-weight:800;font-size:18px;color:var(--white);letter-spacing:.5px;display:flex;align-items:center;gap:8px;white-space:nowrap}
.footer-brand span{width:14px;height:14px;border-radius:50%;background:var(--white)}
.copyright{left:240px;top:48px;font-size:13px;letter-spacing:.5px;white-space:nowrap}
.get-touch{left:749px;top:50px;font-size:13px}
.footer-social{left:864px;top:38px;display:flex;gap:24px}
.footer-social span{width:36px;height:36px;border:2px solid var(--white);border-radius:50%}
</style>
</head>
<body>

<header class="section site-header">
  <div class="abs brand"><span class="brand-dot"></span>PRAXELUN</div>
  <nav class="abs main-nav"><span>SERVICES</span><span>ABOUT US</span><span>CONTACT</span></nav>
  <div class="abs lang">Language : <b>English</b></div>
  <div class="abs social-ring"></div>
</header>

<section class="section hero" role="img" aria-label="Close-up of a circular saw blade with wood shavings">
  <h1 class="abs hero-title">ARE YOU INTERESTED IN AN ESTIMATE?</h1>
  <div class="abs btn-quote">GET A QUOTE</div>
  <div class="abs hero-dots"><span></span><span></span><span class="on"></span><span></span><span></span></div>
</section>

<section class="section woodworks">
  <div class="abs photo" style="top:36px;background:linear-gradient(160deg,#c9b9a6,#7a4a2a 55%,#3d2616)" role="img" aria-label="Kitchen with wooden cabinets and a live-edge wooden counter"></div>
  <h2 class="abs svc-title" style="top:40px">WOODWORKS</h2>
  <p class="abs svc-text" style="top:105px">Timber is, in essence, a natural and warm material. Wood is also relatively durable and easy to work with, which has made it a favourite of builders throughout history. Our goal is to offer suitable products and quality furniture with installation and after sales service to all of our clients. In order to achieve this, we're ready to help our clients in all stages of construction from design to production and maintenance.</p>
  <ul class="abs svc-list" style="top:258px"><li>Furniture</li><li>Staircases</li><li></li><li>Windows</li><li>Woodcarving</li><li></li><li>Doors</li><li>Graining</li><li></li></ul>
</section>

<section class="section stoneworks">
  <div class="abs photo" style="top:50px;background:linear-gradient(150deg,#c9c4bd,#6f6e6c 50%,#3a3a3a)" role="img" aria-label="Hands laying granite paving stones with a rubber mallet"></div>
  <h2 class="abs svc-title" style="top:56px">STONEWORKS</h2>
  <p class="abs svc-text" style="top:116px">The natural stone found in the ground has been used in construction for centuries because of its durability. A structure built by a skilled craftsman from natural stone is unique, genuine and durable, and perfect for our bracing climate. Our experienced craftsmen are ready to help you in all stages of.</p>
  <ul class="abs svc-list" style="top:272px"><li>Walls</li><li>Outdoor kitchens</li><li>Fences</li><li>Terraces</li><li>Fireplaces</li><li></li><li>Paths</li><li>Smokeries</li><li></li></ul>
</section>

<section class="section restoration">
  <div class="abs photo" style="top:40px;background:linear-gradient(90deg,#e9e9e7 0%,#c9232b 20%,#d9dad8 50%,#5a3c26 75%,#e4e4e2 100%)" role="img" aria-label="A red painted chair beside an old wooden bentwood chair"></div>
  <h2 class="abs svc-title" style="top:44px">RESTORATION</h2>
  <p class="abs svc-text" style="top:112px">It's good to see that fixing old things has become popular again in recent years and people are trying to find ways to preserve valuable old windows and pieces of furniture before deciding to replace them. It is possible to give a new life to almost any wooden door, window, piece of furniture or staircase. The extensive experience of our craftsmen will help you achieve the desired result.</p>
  <ul class="abs svc-list" style="top:268px"><li>Furniture</li><li>Staircases</li><li></li><li>Windows</li><li>Floors</li><li></li><li>Doors</li><li>Special Projects</li><li></li></ul>
</section>

<section class="section about">
  <div class="abs photo" style="top:46px;background:linear-gradient(170deg,#9aa487,#c98a63 40%,#9b5a3a 75%,#6d3f28)" role="img" aria-label="Stack of freshly cut timber planks"></div>
  <h2 class="abs svc-title" style="top:50px">ABOUT US</h2>
  <p class="abs svc-text" style="top:112px">Praxelun is a company whose business operations include making wooden products, restoration and building structures from natural stone. All of our products are made by craftsmen and specialists who have extensive experience and knowledge in their fields. The products we offer are always handmade and we take the requests and ideas of the specific client into account We always strive to achieve the best possible quality.</p>
  <div class="abs signoff" style="top:263px">Quality matters,<br>Praxelun</div>
</section>

<section class="section contact" role="img" aria-label="Dark background of wood shavings">
  <h2 class="abs" style="left:82px;top:52px">CONTACT US</h2>
  <div class="abs contact-item" style="top:152px">
    <div class="contact-icon"><svg width="16" height="20" viewBox="0 0 16 20"><path d="M8 1a6 6 0 0 0-6 6c0 4.5 6 12 6 12s6-7.5 6-12a6 6 0 0 0-6-6z" fill="none" stroke="#e8901a" stroke-width="2"/><circle cx="8" cy="7" r="2" fill="#e8901a"/></svg></div>
    <div><div class="contact-label">Location</div><div class="contact-value">Kaskede 12<br>10415 Harbourville, ESTONIA</div></div>
  </div>
  <div class="abs contact-item" style="top:250px">
    <div class="contact-icon"><svg width="18" height="18" viewBox="0 0 18 18"><path d="M4 1l3 4-2 2c1 2.5 3.5 5 6 6l2-2 4 3-2 3C8 17 1 10 1 4z" fill="#e8901a"/></svg></div>
    <div><div class="contact-label">Telephone</div><div class="contact-value">+372 55 01234</div></div>
  </div>
  <div class="abs contact-item" style="top:346px">
    <div class="contact-icon"><svg width="18" height="14" viewBox="0 0 18 14"><rect x="1" y="1" width="16" height="12" fill="none" stroke="#e8901a" stroke-width="2"/><path d="M1 1l8 7 8-7" fill="none" stroke="#e8901a" stroke-width="2"/></svg></div>
    <div><div class="contact-label">Email</div><div class="contact-value">hello@praxelun.ee</div></div>
  </div>

  <h2 class="abs form-title" style="left:495px;top:52px">PLEASE FILL IN THE FOLLOWING FIELDS</h2>
  <div class="abs form-sub" style="left:495px;top:88px">If You Would Like A Price Quote</div>
  <div class="abs field" style="left:495px;top:136px;width:300px;height:39px">Name</div>
  <div class="abs field" style="left:817px;top:136px;width:302px;height:39px">Telephone</div>
  <div class="abs field" style="left:495px;top:193px;width:624px;height:38px">Email Address</div>
  <div class="abs field" style="left:495px;top:247px;width:624px;height:93px">Message</div>
  <div class="abs btn-send">SEND</div>
</section>

<footer class="section site-footer">
  <div class="abs footer-brand"><span></span>PRAXELUN</div>
  <div class="abs copyright">Copyrights 2016 / Allrights Reserved</div>
  <div class="abs get-touch">Get in Touch</div>
  <div class="abs footer-social"><span></span><span></span><span></span><span></span></div>
</footer>

</body>
</html>
```